Help design website for "Brightwater Civic Advisors" to advance the common good

Here is the Google doc link that lays out the design:

https://files.plumrivet.example/sheet/d/7QmTzR2wLx9KpVbN4hJcY8sEaUoFdG3iXkMnPq5rWt6/edit?usp=sharing

Here is the Google drive folder with the logos and photos: https://vault.plumrivet.example/open?id=4HkWp9LzQe2TxRvN8mBaYc3DsUoJfG6

The testimonials are being gathered and will be shared by Friday, 1/4.

The winner will also have to migrate the coding files to my hosting site.

Thank you for your help! Looking forward to seeing your designs.

Target Market(s)

Prospective clients

Industry/Entity Type

Non Profit

Coding

Coded - Design and coding required

Number of Pages Required

5+ page

Requirements
Must have
• Noted in the Google doc regarding layout.
Nice to have

```html
<!DOCTYPE html>
<html lang="en">
<head>
<meta charset="utf-8">
<title>Brightwater Civic Advisors</title>
<link href="https://fonts.googleapis.com/css2?family=Montserrat:wght@500;600;700;800&family=Open+Sans:wght@400;600;700&display=swap" rel="stylesheet">
<style>
:root{
  --blue:#5b8fd3;
  --blue-dark:#3f74bd;
  --navy:#1b2840;
  --ink:#222;
  --muted:#555;
  --grey:#efefef;
  --footer:#e9e9ea;
  --white:#fff;
}
*{box-sizing:border-box;margin:0;padding:0}
html,body{width:1200px;height:5085px;overflow:hidden}
body{position:relative;background:var(--white);font-family:"Open Sans",Arial,sans-serif;color:var(--ink)}
.abs{position:absolute}
.heading{font-family:"Montserrat",Arial,sans-serif;font-weight:700}
.btn{position:absolute;display:flex;align-items:center;justify-content:center;border-radius:30px;background:var(--blue);color:#fff;font-size:17px}
.btn-flow{position:static;width:132px;height:38px;font-size:15px;margin-top:12px}

/* top bar */
.topbar{left:0;top:0;width:1200px;height:166px;background:#fff}
.contact{top:72px;font-size:16px;color:#333;display:flex;align-items:center;gap:10px}
.brand{right:100px;top:34px;display:flex;align-items:center;gap:16px}
.brand-mark{width:64px;height:64px;background:var(--blue)}
.brand-name{font-family:"Montserrat",Arial,sans-serif;font-weight:600;font-size:30px;line-height:1.15;color:var(--navy);letter-spacing:3px;text-transform:uppercase;width:330px}
.nav{left:0;top:166px;width:1200px;height:80px;background:var(--blue);display:flex;justify-content:center;align-items:center;gap:60px;color:#fff;font-size:17px}

/* hero */
.hero{left:0;top:246px;width:1200px;height:610px;background:linear-gradient(180deg,#4c5058,#2e3238 60%,#3b3f46)}
.hero-cut{left:0;top:640px}
.hero-title{left:0;top:370px;width:1200px;text-align:center;color:#fff;font-size:56px;line-height:1.18;text-transform:uppercase;letter-spacing:1px}
.hero-sub{left:0;top:515px;width:1200px;text-align:center;color:#fff;font-size:20px;line-height:1.4}

/* about */
.about-title{left:92px;top:905px;font-size:38px;color:#111}
.about-text{left:92px;top:985px;width:520px;font-size:17px;line-height:1.45;color:#222}
.about-text p{margin-bottom:20px}
.about-photo-shadow{left:689px;top:910px;width:400px;height:396px;background:#fff;box-shadow:0 6px 18px rgba(0,0,0,.25)}
.about-photo{left:671px;top:892px;width:400px;height:396px;background:linear-gradient(135deg,#8a7f78,#4d4643)}

/* services */
.services{left:0;top:1346px;width:1200px;height:700px;background:var(--blue)}
.services-title{left:0;top:1380px;width:1200px;text-align:center;color:#fff;font-size:38px}
.card{position:absolute;width:284px;height:230px}
.card-img{position:absolute;inset:0;background:linear-gradient(135deg,#7a6d60,#3e3a38)}
.card-label{position:absolute;left:24px;right:24px;bottom:22px;background:#fff;text-align:center;font-size:17px;line-height:1.2;color:#222;padding:8px 6px}

/* testimonial */
.testimonial{left:0;top:2046px;width:1200px;height:464px;background:var(--grey)}
.world{left:230px;top:2070px;width:740px;height:420px;background:radial-gradient(ellipse at center,rgba(0,0,0,.05),rgba(0,0,0,0) 70%)}
.testi-title{left:0;top:2092px;width:1200px;text-align:center;font-size:36px;color:#111}
.avatar{left:584px;top:2165px;width:92px;height:92px;border-radius:50%;background:linear-gradient(135deg,#8b6d5c,#4a3a31)}
.quote{left:190px;top:2308px;width:820px;text-align:center;font-size:16.5px;line-height:1.6;color:#333}
.quote-mark{font-family:Georgia,serif;color:var(--blue);font-size:28px;line-height:0;vertical-align:-6px;margin:0 6px}
.quote-by{left:0;top:2438px;width:1200px;text-align:center;font-size:16px;color:var(--blue-dark);font-weight:600}

/* media */
.media-title{left:0;top:2565px;width:1200px;text-align:center;font-size:38px;color:#111}
.post{position:absolute;display:flex;flex-direction:column;align-items:flex-start}
.post-title{font-size:26px;line-height:1.22;color:#111;margin-bottom:16px}
.meta{font-size:14px;color:#333;font-weight:700;display:flex;gap:40px;margin-bottom:14px}
.post-text{font-size:16px;line-height:1.55;color:#333}
.post-img{background:linear-gradient(135deg,#6f6862,#2f2b2a)}
.date{position:absolute;width:78px;height:78px;background:var(--blue);transform:rotate(45deg)}
.date-txt{position:absolute;width:78px;text-align:center;color:#fff;font-weight:700;font-size:15px;line-height:1.15}

/* consultation */
.consult{left:0;top:3900px;width:1200px;height:795px;background:linear-gradient(180deg,rgba(88,140,210,.93),rgba(70,120,196,.95))}
.consult-title{left:0;top:4025px;width:1200px;text-align:center;color:#fff;font-size:36px}
.field{position:absolute;left:329px;width:535px;height:36px;background:#fff;font-size:14px;color:#444;padding:9px 14px}
.submit{left:516px;top:4598px;width:138px;height:36px;border-radius:20px;background:#000;color:#fff;display:flex;align-items:center;justify-content:center;font-size:17px}

/* footer */
.footer{left:0;top:4695px;width:1200px;height:390px;background:var(--footer)}
.foot-brand{left:92px;top:4800px;display:flex;align-items:center;gap:16px}
.foot-brand .brand-name{font-size:28px;width:300px}
.foot-h{font-size:24px;color:#111}
.foot-links{left:540px;top:4830px;font-size:16px;line-height:2.05;color:#222}
.email{left:780px;top:4824px;width:320px;height:42px;border-radius:22px;background:#fff;border:1px solid #ccc;font-size:14px;color:#333;padding:11px 20px}
.send{left:888px;top:4884px;width:104px;height:32px;border-radius:18px;background:#fff;border:1px solid #999;font-size:14px;display:flex;align-items:center;justify-content:center}
.copy{left:92px;top:5030px;font-size:15px;color:#333}
.social{top:5028px;width:22px;height:22px;background:var(--blue)}
</style>
</head>
<body>

<header class="abs topbar">
  <div class="abs contact" style="left:110px">
    <svg width="22" height="22" viewBox="0 0 24 24"><path d="M6.6 10.8a15 15 0 0 0 6.6 6.6l2.2-2.2c.3-.3.7-.4 1-.2 1.1.4 2.3.6 3.6.6.6 0 1 .4 1 1V20c0 .6-.4 1-1 1A17 17 0 0 1 3 4c0-.6.4-1 1-1h3.5c.6 0 1 .4 1 1 0 1.3.2 2.5.6 3.6.1.3 0 .7-.2 1z" fill="#5b8fd3"/></svg>
    <span>(415) 555-0148</span>
  </div>
  <div class="abs contact" style="left:290px">
    <svg width="22" height="18" viewBox="0 0 24 18"><rect x="1" y="1" width="22" height="16" fill="none" stroke="#5b8fd3" stroke-width="2"/><path d="M1 1l11 9 11-9" fill="none" stroke="#5b8fd3" stroke-width="2"/></svg>
    <span>dana@brightwatercivic.example</span>
  </div>
  <div class="abs brand">
    <div class="brand-mark"></div>
    <div class="brand-name">Brightwater Civic Advisors</div>
  </div>
</header>

<nav class="abs nav">
  <span>About</span>
  <span>Services &amp; Testimonials &#9662;</span>
  <span>Media &amp; Impact &#9662;</span>
  <span>Contact</span>
</nav>

<section>
  <div class="abs hero" role="img" aria-label="Photo of an audience at a workshop, darkened"></div>
  <svg class="abs hero-cut" width="1200" height="220" viewBox="0 0 1200 220"><polygon points="0,70 600,216 1200,70 1200,220 0,220" fill="#fff"/></svg>
  <h1 class="abs heading hero-title">Welcome to Brightwater<br>Civic Advisors</h1>
  <p class="abs hero-sub">Nonprofit Organizations And Educational Institutions To Carry Out Their Missions To<br>Benefit The Wider Community.</p>
  <div class="btn" style="left:490px;top:608px;width:218px;height:56px;font-size:19px">View More</div>
</section>

<section>
  <h2 class="abs heading about-title">ABOUT ME</h2>
  <div class="abs about-text">
    <p>Brightwater Civic Advisors supports nonprofit organizations and educational institutions to carry out their missions to benefit the wider community.</p>
    <p>Founder Dana Lin is an educator with a 22-year record of demonstrated achievement and leadership roles in nonprofits and educational institutions. Most recently, she served as Associate Dean of Students in the University and Director of the University Community Service Center at Lakeshore University. Dana has</p>
  </div>
  <div class="btn" style="left:92px;top:1230px;width:178px;height:52px">Read More</div>
  <div class="abs about-photo-shadow"></div>
  <div class="abs about-photo" role="img" aria-label="Portrait photo of the founder"></div>
</section>

<section>
  <div class="abs services"></div>
  <h2 class="abs heading services-title">Services</h2>
  <div class="card" style="left:142px;top:1478px"><div class="card-img" role="img" aria-label="Photo of smiling staff"></div><div class="card-label">Staff Professional<br>Development</div></div>
  <div class="card" style="left:458px;top:1478px"><div class="card-img" role="img" aria-label="Photo of a community group"></div><div class="card-label">Community Partnership<br>Development</div></div>
  <div class="card" style="left:773px;top:1478px"><div class="card-img" role="img" aria-label="Photo of a group discussion"></div><div class="card-label">Group Facilitation &amp;<br>Leadership Training</div></div>
  <div class="card" style="left:142px;top:1763px"><div class="card-img" role="img" aria-label="Photo of a large group of volunteers"></div><div class="card-label">Program Design,<br>Implementation,<br>&amp; Evaluation</div></div>
  <div class="card" style="left:458px;top:1763px"><div class="card-img" role="img" aria-label="Photo of a speaker at an event"></div><div class="card-label">Event<br>Planning</div></div>
  <div class="card" style="left:773px;top:1763px"><div class="card-img" role="img" aria-label="Photo of a strategy presentation"></div><div class="card-label">Strategic Planning<br>&amp; Visioning</div></div>
</section>

<section>
  <div class="abs testimonial"></div>
  <div class="abs world" role="img" aria-label="Faint dotted world map"></div>
  <h2 class="abs heading testi-title">Testimonial</h2>
  <div class="abs avatar" role="img" aria-label="Photo of the reviewer"></div>
  <svg class="abs" style="left:88px;top:2326px" width="14" height="24" viewBox="0 0 14 24"><path d="M12 2L3 12l9 10" fill="none" stroke="#5b8fd3" stroke-width="3"/></svg>
  <svg class="abs" style="left:1095px;top:2326px" width="14" height="24" viewBox="0 0 14 24"><path d="M2 2l9 10-9 10" fill="none" stroke="#5b8fd3" stroke-width="3"/></svg>
  <p class="abs quote"><span class="quote-mark">&ldquo;</span>Dana has an uncanny ability to combine social change theory and real-world practice in truly compelling ways. For five years at Lakeshore University, I saw first-hand how Dana inspired legions of students, created innovative programs, and transformed relationships with community stakeholders. Best of all, she did it with integrity, smarts, enthusiasm and a warm, infectious spirit.<span class="quote-mark">&rdquo;</span></p>
  <p class="abs quote-by">- Reena Wallace, VP, Chief Content Officer, WLKR</p>
</section>

<section>
  <h2 class="abs heading media-title">Media &amp; Impact</h2>

  <article class="post" style="left:92px;top:2698px;width:470px">
    <h3 class="heading post-title">LUCSC Open Exchange Program Celebrates First Year</h3>
    <div class="meta"><span>BY: ADMIN</span><span>COMMENTS : 0</span></div>
    <p class="post-text">Students and participants of the University's Community Service Center's (LUCSC) Open Exchange program reflected on the work that they had done with immigrants and refugees in various communities across the city. Harbor Cafe held a dinner for the participants on May 9.</p>
    <div class="btn btn-flow">Read More</div>
  </article>
  <div class="abs post-img" style="left:593px;top:2705px;width:515px;height:332px" role="img" aria-label="Photo of a program dinner in a hall"></div>
  <div class="date" style="left:554px;top:2790px"></div>
  <div class="date-txt" style="left:554px;top:2800px">Jan<br>04<br>2019</div>

  <div class="abs post-img" style="left:92px;top:3153px;width:468px;height:322px" role="img" aria-label="Video still of young volunteers"></div>
  <div class="date" style="left:521px;top:3245px"></div>
  <div class="date-txt" style="left:521px;top:3255px">Jan<br>04<br>2019</div>
  <article class="post" style="left:640px;top:3160px;width:470px">
    <h3 class="heading post-title">Hundreds of young volunteers think globally, act locally</h3>
    <div class="meta"><span>BY: ADMIN</span><span>COMMENTS : 0</span></div>
    <p class="post-text">CHICAGO &mdash; A day of action brought hundreds of volunteers to the South Side Sunday, including former First Daughter Marisa Holt, capping off a three-day event sponsored by the Open Horizons Initiative.</p>
    <div class="btn btn-flow">Read More</div>
  </article>

  <article class="post" style="left:92px;top:3568px;width:470px">
    <h3 class="heading post-title">Lakeshore Ledger, MLK Day of Service (January 2018)</h3>
    <div class="meta"><span>BY: ADMIN</span><span>COMMENTS : 0</span></div>
    <p class="post-text">The first episode of the Lakeshore Ledger's Monday morning news show.<br>Hosts: Noah Pratt, Evan Kessler<br>Featuring: Lila Moore, Sam Reyes, Dana Lin<br>Music: Theo Marsh</p>
    <div class="btn btn-flow">Read More</div>
  </article>
  <div class="abs" style="left:593px;top:3583px;width:515px;height:230px;background:linear-gradient(135deg,#8a6a68,#5a4240)" role="img" aria-label="Podcast player artwork for the news show episode"></div>
  <div class="date" style="left:554px;top:3660px"></div>
  <div class="date-txt" style="left:554px;top:3670px">Jan<br>04<br>2019</div>
</section>

<section>
  <div class="abs consult" role="img" aria-label="Photo of a group with a blue overlay"></div>
  <h2 class="abs heading consult-title">Book a complimentary consultation</h2>
  <div class="field" style="top:4134px">First Name</div>
  <div class="field" style="top:4197px">Last Name</div>
  <div class="field" style="top:4258px">Organization Name</div>
  <div class="field" style="top:4322px">Email Address</div>
  <div class="field" style="top:4384px">Service You need</div>
  <div class="field" style="top:4446px;height:114px">Messages</div>
  <div class="abs submit">Submit</div>
</section>

<footer>
  <div class="abs footer"></div>
  <div class="abs foot-brand">
    <div class="brand-mark"></div>
    <div class="brand-name">Brightwater Civic Advisors</div>
  </div>
  <h4 class="abs heading foot-h" style="left:540px;top:4780px">LINKS</h4>
  <div class="abs foot-links">About<br>Services &amp; Testimonials<br>Media &amp; Impact<br>Contact</div>
  <h4 class="abs heading foot-h" style="left:868px;top:4780px">News Letter</h4>
  <div class="abs email">Enter the Email</div>
  <div class="abs send">Send</div>
  <div class="abs" style="left:92px;top:5010px;width:1016px;height:1px;background:#ccc"></div>
  <p class="abs copy">&copy; 2019 Brightwater Civic Advisors &nbsp;All rights reserved</p>
  <div class="abs social" style="left:972px"></div>
  <div class="abs social" style="left:1000px"></div>
  <div class="abs social" style="left:1028px"></div>
  <div class="abs social" style="left:1056px"></div>
  <div class="abs social" style="left:1084px"></div>
</footer>

</body>
</html>
```